Velk Consulting -New consulting business in architecture, urban planning, and real estate development

We need a stationery design, including logo, business cards, etc, work for a new consulting business that works in the world of architectural, urban planning and real estate development.

The name of the company is "Velk Consulting". Velk is my last name but it of course also has the meaning 'cool' and 'hip'.

Target Market(s)

The business will provide boutique consulting services to high end clients that may include property developers, cities, etc.

Industry/Entity Type

Consultant

Contact Information for Business Card

VELK Consulting
First Name Last Name
Title
Phone number
Address
Website
Optional: Twitter handle

Logo Text

VELK Consulting

Font styles to use
Sans Serif

Colors

Designer to choose colors to be used in the design.

Requirements
Must have
• Simple design
• Easy to read font
• Modern
• Elegance
• Nice font that can be used for future reports, letters, etc.
• Good colour scheme that allows for the elegance to come through
Should not have
• Complex design ideas
• Complex logos
• Not a corporate feel and look

```html
<!DOCTYPE html>
<html lang="en">
<head>
<meta charset="utf-8">
<title>Velk Consulting – Stationery</title>
<link href="https://fonts.googleapis.com/css2?family=Montserrat:wght@400;500;600&display=swap" rel="stylesheet">
<style>
  :root {
    --gold: #a88a22;
    --gold-soft: #c4a444;
    --paper: #f4f4f3;
    --ink: #2c2c2c;
    --ink-soft: #6a6a6a;
    --desk-top: #ebebea;
    --desk-bottom: #d4e2e8;
  }
  * { margin: 0; padding: 0; box-sizing: border-box; }
  html, body { width: 1200px; height: 1181px; overflow: hidden; }
  body { position: relative; font-family: "Montserrat", sans-serif; color: var(--ink); background: var(--desk-top); }

  .surface-top { position: absolute; left: 0; top: 0; width: 1200px; height: 739px; background: var(--desk-top); }
  .surface-bottom { position: absolute; left: 0; top: 739px; width: 1200px; height: 442px; background: var(--desk-bottom); }

  .wordmark { color: var(--gold); font-weight: 500; font-size: 13px; letter-spacing: 2.5px; text-transform: uppercase; white-space: nowrap; text-align: center; }

  /* Letterhead */
  .letterhead { position: absolute; width: 416px; height: 584px; background: var(--paper); box-shadow: 0 1px 3px rgba(0,0,0,.12); }
  .letterhead.back { left: 502px; top: 38px; }
  .letterhead.front { left: 410px; top: 121px; }
  .letterhead .frame { position: absolute; inset: 13px; border: 1px solid var(--gold); }
  .letterhead .wordmark { position: absolute; left: 0; right: 0; top: 48px; }
  .recipient { position: absolute; left: 49px; top: 161px; font-size: 7.6px; line-height: 9.4px; color: var(--ink-soft); }
  .recipient strong { color: var(--ink); font-weight: 600; }
  .letter-date { position: absolute; right: 34px; top: 189px; font-size: 7.6px; color: var(--ink-soft); letter-spacing: .3px; }
  .letter-body { position: absolute; left: 37px; width: 342px; top: 231px; font-size: 5.7px; line-height: 12.4px; color: var(--ink-soft); text-align: justify; }
  .letter-body p { text-indent: 8px; margin-bottom: 13px; }

  .contact { position: absolute; left: 0; right: 0; text-align: center; font-size: 5.4px; color: var(--ink); }
  .contact .address strong { font-weight: 600; }
  .contact .channels { display: flex; justify-content: center; align-items: center; margin-top: 6px; }
  .contact .channel { display: flex; align-items: center; gap: 3px; padding: 0 6px; }
  .contact .channel + .channel { border-left: 1px solid #9a9a9a; }
  .contact svg { width: 7px; height: 7px; }
  .letterhead .contact { top: 537px; }

  /* Envelopes */
  .envelope-open { position: absolute; left: 128px; top: 830px; width: 444px; height: 302px; }
  .envelope-open .liner { position: absolute; left: 0; top: 0; width: 444px; height: 302px; }
  .envelope-open .wordmark { position: absolute; left: 0; right: 0; top: 208px; }

  .envelope-closed { position: absolute; left: 642px; top: 906px; width: 450px; height: 224px; background: var(--paper); box-shadow: 6px 8px 14px rgba(60,80,90,.25); }
  .envelope-closed .frame { position: absolute; inset: 13px; border: 1px solid var(--gold); }
  .envelope-closed .wordmark { position: absolute; left: 31px; top: 42px; }
  .envelope-closed .contact { left: 31px; right: auto; top: 175px; text-align: left; }
  .envelope-closed .contact .channels { justify-content: flex-start; }
  .envelope-closed .contact .channel:first-child { padding-left: 0; }
</style>
</head>
<body>
  <div class="surface-top"></div>
  <div class="surface-bottom"></div>

  <svg width="0" height="0" style="position:absolute">
    <defs>
      <symbol id="icon-phone" viewBox="0 0 10 10"><path d="M2.2 1 L3.8 2.8 L3 3.9 C3.6 5.2 4.8 6.4 6.1 7 L7.2 6.2 L9 7.8 L8 9 C4.6 8.8 1.2 5.4 1 2 Z" fill="none" stroke="#a88a22" stroke-width="1"/></symbol>
      <symbol id="icon-mail" viewBox="0 0 10 10"><rect x="1" y="2.5" width="8" height="5.5" fill="none" stroke="#a88a22" stroke-width=".9"/><path d="M1 2.5 L5 5.8 L9 2.5" fill="none" stroke="#a88a22" stroke-width=".9"/></symbol>
      <symbol id="icon-web" viewBox="0 0 10 10"><circle cx="5" cy="5" r="4" fill="none" stroke="#a88a22" stroke-width=".9"/><ellipse cx="5" cy="5" rx="1.8" ry="4" fill="none" stroke="#a88a22" stroke-width=".7"/><path d="M1 5 H9" stroke="#a88a22" stroke-width=".7"/></symbol>
    </defs>
  </svg>

  <!-- Back letterhead sheet -->
  <section class="letterhead back">
    <div class="frame"></div>
    <div class="wordmark">VELK Consulting</div>
    <div class="letter-date">Date : 01 July 2018</div>
    <div class="letter-body">
      <p>Lorem ipsum dolor sit amet, justo platonem in per, dicant constituto ne eam. Aeque persecuti sit ea, at vis commodo tractatos vituperata, sea an albucius forensibus. Wisi quodsi id qui, duo tempor aliquam assentior eu, no diceret tibique definiebas mei.</p>
      <p>Nullam definiebas signiferumque pro te, vel mutat lobortis conceptam in. Usu justo minimum an, ne regione sanctus praesent usu, eam ut adipisci volutpat. Vel odio tibique consequat ne, in dicit gubergren appellantur vis, quo ei omnis elitr. Qui ne enim dictas dissentiet, pro nulla quodsi deseruisse te. Vide prima eloquentiam pro ei, agam dicta in pro, eu persius propriae constituam sea. Ius ut iriure oblique laboramus, cu sed fugit commune invenire, viris repudiandae ex vis. Nullam definiebas signiferumque pro te, vel mutat lobortis conceptam in. Usu justo minimum an, ne regione sanctus praesent usu, eam ut adipisci volutpat. Vel odio tibique consequat ne, in dicit gubergren appellantur vis, quo ei omnis elitr. Qui ne enim dictas dissentiet, pro nulla quodsi deseruisse te. Vide prima eloquentiam pro ei, agam dicta in pro, eu persius propriae constituam sea. Ius ut iriure oblique laboramus, cu sed fugit commune invenire, viris repudiandae ex vis.</p>
    </div>
  </section>

  <!-- Front letterhead sheet -->
  <section class="letterhead front">
    <div class="frame"></div>
    <div class="wordmark">VELK Consulting</div>
    <div class="recipient">
      <strong>MR. Aaron BELLAMY</strong><br>
      <strong>Managing Director</strong><br>
      12/08 Linden Court<br>
      Oregon - 987654321
    </div>
    <div class="letter-date">Date : 01 July 2018</div>
    <div class="letter-body">
      <p>Lorem ipsum dolor sit amet, justo platonem in per, dicant constituto ne eam. Aeque persecuti sit ea, at vis commodo tractatos vituperata, sea an albucius forensibus. Wisi quodsi id qui, duo tempor aliquam assentior eu, no diceret tibique definiebas mei. Id nec noster facilisi mandamus.</p>
      <p>Nullam definiebas signiferumque pro te, vel mutat lobortis conceptam in. Usu justo minimum an, ne regione sanctus praesent usu, eam ut adipisci volutpat. Vel odio tibique consequat ne, in dicit gubergren appellantur vis, quo ei omnis elitr. Qui ne enim dictas dissentiet, pro nulla quodsi deseruisse te. Vide prima eloquentiam pro ei, agam dicta in pro, eu persius propriae constituam sea. Ius ut iriure oblique laboramus, cu sed fugit commune invenire, viris repudiandae ex vis. Nullam definiebas signiferumque pro te, vel mutat lobortis conceptam in. Usu justo minimum an, ne regione sanctus praesent usu, eam ut adipisci volutpat. Vel odio tibique consequat ne, in dicit gubergren appellantur vis, quo ei omnis elitr. Qui ne enim dictas dissentiet, pro nulla quodsi deseruisse te. Vide prima eloquentiam pro ei, agam dicta in pro, eu persius propriae constituam sea. Ius ut iriure oblique laboramus, cu sed fugit commune invenire, viris repudiandae ex vis. Nullam definiebas signiferumque pro te, vel mutat lobortis conceptam in. Usu justo minimum an, ne regione sanctus praesent usu, eam ut adipisci volutpat. Vel odio tibique consequat ne, in dicit gubergren appellantur vis, quo ei omnis elitr. Qui ne enim dictas dissentiet, pro nulla quodsi deseruisse te. Vide prima eloquentiam pro ei, agam dicta in pro, eu persius propriae constituam sea. Ius ut iriure oblique laboramus, cu sed fugit commune invenire, viris repudiandae ex vis.</p>
    </div>
    <div class="contact">
      <div class="address"><strong>Velk Consulting</strong> - 418 Harlow Avenue, Fairmont, OR 97401</div>
      <div class="channels">
        <span class="channel"><svg><use href="#icon-phone"/></svg>000 000 0000</span>
        <span class="channel"><svg><use href="#icon-mail"/></svg>info@velkconsulting.com</span>
        <span class="channel"><svg><use href="#icon-web"/></svg>www.velkconsulting.com</span>
      </div>
    </div>
  </section>

  <!-- Open envelope with patterned liner -->
  <section class="envelope-open">
    <svg class="liner" viewBox="0 0 444 302">
      <path d="M24 10 Q26 2 36 2 L408 2 Q418 2 420 10 L444 92 L0 92 Z" fill="var(--gold-soft)" role="img" aria-label="Gold ornamental pattern on the envelope liner"/>
      <path d="M0 92 L444 92 L444 302 L0 302 Z" fill="#ecebee"/>
      <path d="M0 92 L120 140 L324 140 L444 92 Z" fill="#f4f4f6"/>
      <path d="M40 134 Q42 124 54 124 L390 124 Q402 124 404 134 L444 302 L0 302 Z" fill="var(--paper)"/>
    </svg>
    <div class="wordmark">VELK Consulting</div>
  </section>

  <!-- Closed envelope front -->
  <section class="envelope-closed">
    <div class="frame"></div>
    <div class="wordmark">VELK Consulting</div>
    <div class="contact">
      <div class="address"><strong>Velk Consulting</strong> - 418 Harlow Avenue, Fairmont, OR 97401</div>
      <div class="channels">
        <span class="channel"><svg><use href="#icon-phone"/></svg>000 000 0000</span>
        <span class="channel"><svg><use href="#icon-mail"/></svg>info@velkconsulting.com</span>
        <span class="channel"><svg><use href="#icon-web"/></svg>www.velkconsulting.com</span>
      </div>
    </div>
  </section>
</body>
</html>
```